Corporate Business Card

Very professional, Modern, Not to busy, include phone address email, website
(253) 617-4930, 18761 52nd Avenue S, Kent, WA 98047, martin@plumlinegroup.com, varkoworks.com

Target Market(s)

Manufacturing

Industry/Entity Type

Aero, machining, manufacturing, Off road racing

Contact Information for Business Card

Phone, address email, website

```html
<!DOCTYPE html>
<html lang="en">
<head>
<meta charset="utf-8">
<title>Varko Works – Business Card</title>
<link href="https://fonts.googleapis.com/css2?family=Montserrat:wght@500;700&display=swap" rel="stylesheet">
<style>
  :root {
    --red: #d1232a;
    --navy: #1c3a7a;
    --white: #ffffff;
    --ink: #1e1e1e;
    --backdrop: #d9d9d9;
  }
  * { box-sizing: border-box; margin: 0; padding: 0; }
  html, body { width: 1200px; height: 900px; overflow: hidden; }
  body {
    background: var(--backdrop);
    font-family: "Montserrat", Arial, sans-serif;
    position: relative;
  }
  .card {
    position: absolute;
    left: 250px;
    width: 700px;
    height: 400px;
    overflow: hidden;
    box-shadow: 0 4px 14px rgba(0,0,0,0.18);
  }
  .card--front { top: 35px; background: var(--red); }
  .card--back { top: 465px; background: var(--white); }

  .brand {
    position: absolute;
    font-weight: 700;
    letter-spacing: 1px;
    line-height: 1;
    white-space: nowrap;
  }
  .card--front .brand {
    color: var(--white);
    font-size: 78px;
    left: 120px;
    top: 140px;
  }
  .brand-rule {
    position: absolute;
    height: 3px;
  }
  .card--front .brand-rule {
    background: var(--white);
    left: 120px;
    top: 250px;
    width: 240px;
  }
  .card--back .brand {
    color: var(--navy);
    font-size: 50px;
    left: 330px;
    top: 50px;
  }
  .card--back .brand-rule {
    background: var(--navy);
    left: 330px;
    top: 122px;
    width: 160px;
    height: 2px;
  }

  .wave { position: absolute; inset: 0; }

  .address {
    position: absolute;
    left: 70px;
    top: 160px;
    font-size: 17px;
    font-weight: 500;
    color: var(--ink);
    line-height: 1.4;
  }
  .contact-list {
    position: absolute;
    left: 70px;
    top: 250px;
    list-style: none;
    font-size: 17px;
    font-weight: 500;
    color: var(--ink);
  }
  .contact-list li {
    display: flex;
    align-items: center;
    gap: 12px;
    height: 30px;
  }
  .contact-list svg { width: 18px; height: 18px; flex: none; }
</style>
</head>
<body>

  <section class="card card--front">
    <div class="brand">Varko Works</div>
    <div class="brand-rule"></div>
  </section>

  <section class="card card--back">
    <svg class="wave" viewBox="0 0 700 400" preserveAspectRatio="none">
      <path d="M250 400 C310 330 400 315 490 295 C590 272 660 200 700 100 L700 400 Z" fill="var(--red)"/>
      <path d="M250 400 C310 330 400 315 490 295 C590 272 660 200 700 100" fill="none" stroke="var(--navy)" stroke-width="4"/>
    </svg>

    <div class="brand">Varko Works</div>
    <div class="brand-rule"></div>

    <p class="address">18761 52nd Avenue<br>S, Kent, WA 98047</p>

    <ul class="contact-list">
      <li>
        <svg viewBox="0 0 20 20" aria-hidden="true"><path d="M5 2h3l1.5 4-2 1.5a10 10 0 0 0 5 5L14 10.5l4 1.5v3a2 2 0 0 1-2 2A14 14 0 0 1 3 4a2 2 0 0 1 2-2z" fill="var(--red)"/></svg>
        (253) 617-4930
      </li>
      <li>
        <svg viewBox="0 0 20 20" aria-hidden="true"><rect x="2" y="4" width="16" height="12" rx="1" fill="var(--red)"/><path d="M2.5 5l7.5 6 7.5-6" fill="none" stroke="var(--white)" stroke-width="1.5"/></svg>
        martin@plumlinegroup.com
      </li>
      <li>
        <svg viewBox="0 0 20 20" aria-hidden="true"><circle cx="10" cy="10" r="8" fill="var(--red)"/><ellipse cx="10" cy="10" rx="3.5" ry="8" fill="none" stroke="var(--white)" stroke-width="1.2"/><path d="M2 10h16" stroke="var(--white)" stroke-width="1.2"/></svg>
        www.varkoworks.com
      </li>
    </ul>
  </section>

</body>
</html>
```